Breakthrough book for CEO's for navigating exponential change (very timely!)

This book changes the way leaders approach change. It comes from deep experience - seeing first hand what isn't working. It will be a book still being purchased in 5 or 10 years time, and broadly quoted. The author is female, doesn't want to shown up as "look at me" (the work is the hero) but needs to command authority among C-Suite which skews strongly male. The book is about systems thinking, hence why I've been exploring designs that cue "systems" (attached). It would be good to keep exploring this theme, along with others. Attached are files which give more background: including author / brand guidelines, a design brief, Bring your creativity and energy - and help me connect and cut through to the people who really need this book!

Target Market(s)

CEO's, Senior Executive Leaders

Industry/Entity Type

Business, Corporate

Font styles to use
Other font styles liked:
• See the brief: Raleway and Beyond Infinity

Colors

Designer to choose colors to be used in the design.

Requirements
Must have
• Implicit authority and deep insight. This is a book that says there is depth beyond the cover
Nice to have
• See the brief
Should not have
• the usual arrows, bridges and a shouting style.

```html
<!DOCTYPE html>
<html lang="en">
<head>
<meta charset="utf-8">
<title>Leading Deep Renewal — Book Cover</title>
<link rel="stylesheet" href="https://fonts.googleapis.com/css2?family=Cormorant+Garamond:wght@500;600&family=Cinzel:wght@400&family=Raleway:wght@400;500&family=Mrs+Saint+Delafield&family=Libre+Baskerville&display=swap">
<style>
  :root {
    --page: #faf9f7;
    --crimson: #8a002d;
    --crimson-deep: #4a0017;
    --cream: #fbe8cf;
    --white: #ffffff;
    --role: #f1e6e6;
    --burst-core: #8e0f2a;
  }
  * { margin: 0; padding: 0; box-sizing: border-box; }
  html, body { width: 1200px; height: 937px; overflow: hidden; background: var(--page); }
  .canvas { position: relative; width: 1200px; height: 937px; }

  .cover {
    position: absolute; left: 53px; top: 82px; width: 1098px; height: 733px;
    background:
      radial-gradient(ellipse 420px 320px at 330px 330px, rgba(190,10,70,0.55), transparent 70%),
      linear-gradient(to bottom, var(--crimson) 0%, #950033 55%, #6e0024 85%, var(--crimson-deep) 100%);
    box-shadow: 0 22px 26px -12px rgba(0,0,0,0.35);
    color: var(--white);
  }

  .script-title {
    font-family: "Mrs Saint Delafield", cursive;
    font-weight: 400; color: var(--white); white-space: nowrap;
  }
  .series { font-family: "Libre Baskerville", serif; letter-spacing: 0.12em; white-space: nowrap; }

  /* Back cover */
  .back { position: absolute; left: 0; top: 0; width: 518px; height: 733px; text-align: center; }
  .back .script-title { position: absolute; left: 0; width: 536px; top: 26px; font-size: 74px; line-height: 46px; }
  .back .series { position: absolute; left: 0; width: 536px; top: 130px; font-size: 13.5px; }
  .blurb {
    position: absolute; left: 46px; width: 444px; top: 161px;
    font-family: "Raleway", sans-serif; font-size: 15.2px; line-height: 17.8px;
  }
  .blurb p + p { margin-top: 8px; }
  .divider { position: absolute; left: 183px; top: 469px; width: 166px; height: 2px; background: var(--white); }
  .author-photo {
    position: absolute; left: 51px; top: 489px; width: 91px; height: 87px;
    background: linear-gradient(160deg, #ece6df 0%, #d9b78a 45%, #3f6fb8 100%);
  }
  .author-bio {
    position: absolute; left: 149px; top: 490px; width: 340px;
    font-family: "Raleway", sans-serif; font-size: 9.8px; line-height: 12.4px;
    text-align: justify; text-align-last: left;
  }
  .brand-mark {
    position: absolute; left: 0; width: 536px; top: 602px;
    display: flex; flex-direction: column; align-items: center; gap: 12px;
  }
  .brand-dot { width: 44px; height: 44px; border: 2px solid var(--white); border-radius: 50%; }
  .brand-name { font-family: "Raleway", sans-serif; font-weight: 500; font-size: 23px; letter-spacing: 0.08em; }

  /* Spine */
  .spine { position: absolute; left: 518px; top: 0; width: 130px; height: 733px; }
  .spine-dot { position: absolute; left: 20px; top: 30px; width: 36px; height: 36px; border: 2px solid var(--white); border-radius: 50%; }
  .spine-title {
    position: absolute; left: 36px; top: 99px; writing-mode: vertical-rl;
    font-family: "Cormorant Garamond", serif; font-weight: 500; font-size: 33px;
    color: var(--cream); letter-spacing: 0.01em; white-space: nowrap;
  }
  .spine-title sup, .front-title sup { font-size: 0.4em; vertical-align: super; }
  .spine-author {
    position: absolute; left: 6px; top: 190px; height: 362px; writing-mode: vertical-rl;
    display: flex; align-items: center; gap: 10px;
    font-family: "Cinzel", serif; font-size: 19px; color: var(--white); white-space: nowrap;
  }
  .spine-author .rule { width: 1.5px; flex: 1; background: var(--white); }

  /* Front cover */
  .front { position: absolute; left: 648px; top: 0; width: 450px; height: 733px; text-align: center; }
  .front-title {
    position: absolute; left: 0; width: 450px; top: 52px;
    font-family: "Cormorant Garamond", serif; font-weight: 600; font-size: 66px;
    line-height: 53px; color: var(--cream);
  }
  .burst {
    position: absolute; left: 20px; top: 215px; width: 430px; height: 420px; border-radius: 50%;
    background: radial-gradient(circle, var(--burst-core) 0%, #b8452f 18%, rgba(242,162,74,0.75) 30%, rgba(230,110,60,0.35) 55%, transparent 72%);
  }
  .front .script-title { position: absolute; left: 0; width: 470px; top: 372px; font-size: 58px; line-height: 34px; }
  .front .series { position: absolute; left: 0; width: 470px; top: 448px; font-size: 10.5px; }
  .front-author {
    position: absolute; left: 0; width: 450px; top: 620px;
    font-family: "Cinzel", serif; font-size: 30px; color: var(--white); letter-spacing: 0.02em;
  }
  .front-role {
    position: absolute; left: 0; width: 450px; top: 663px;
    font-family: "Raleway", sans-serif; font-size: 11.5px; letter-spacing: 0.3em; color: var(--role);
  }
</style>
</head>
<body>
<div class="canvas">
  <div class="cover">

    <section class="back">
      <h2 class="script-title">shift without<br>shatter</h2>
      <p class="series">The Leadership Compass</p>
      <div class="blurb">
        <p>Lorem ipsum dolor sit amet, consectetur adipiscing elit, sed do eiusmod tempor incididunt ut labore et dolore magna aliqua. Ut enim ad minim veniam, quis nostrud exercitation ullamco laboris nisi ut aliquip ex ea commodo consequat Duis aute irure dolor in repreenderit in voluptate velit esse cillum dolore eu fugiat nulla pariatur. Excepteur, sint occaecat cupidatat non proident, sunt in culpa qui officia deserunt mollit anim id es laborum.</p>
        <p>Lorem ipsum dolor sit amet, consectetur adipiscing elit, sed do eiusmod tempor incididunt ut labore et dolore magna aliqua. Ut enim ad minim veniam, quis nostrud exercitation ullamco laboris nisi ut aliquip ex ea commodo consequat Duis aute irure dolor in repreenderit in voluptate velit esse cillum dolore eu fugiat nulla pariatur. Excepteur, sint occaecat cupidatat non proident, sunt in culpa qui officia deserunt mollit anim id es laborum.</p>
      </div>
      <div class="divider"></div>
      <div class="author-photo" role="img" aria-label="Author portrait photograph"></div>
      <p class="author-bio">Lorem ipsum dolor sit amet, consectetur adipiscing elit, sed do eiusmod tempor incididunt ut labore et dolore magna aliqua. Ut enim ad minim veniam, quis nostrud exercitation ullamco laboris nisi ut aliquip ex ea commodo consequat Duis aute irure dolor in repreenderit in voluptate velit esse cillum dolore eu fugiat nulla pariatur. Excepteur, sint occaecat cupidatat non proident, sunt in culpa qui officia deserunt mollit anim id es laborum.</p>
      <div class="brand-mark">
        <span class="brand-dot"></span>
        <span class="brand-name">Helena Marchbank</span>
      </div>
    </section>

    <section class="spine">
      <span class="spine-dot"></span>
      <div class="spine-title">LEADING DEEP RENEWAL<sup>TM</sup></div>
      <div class="spine-author"><span class="rule"></span>Helena Marchbank<span class="rule"></span></div>
    </section>

    <section class="front">
      <h1 class="front-title">LEADING<br>DEEP<br>RENEWAL<sup>TM</sup></h1>
      <div class="burst" role="img" aria-label="Radiating golden starburst illustration"></div>
      <h2 class="script-title">shift without<br>shatter</h2>
      <p class="series">The Leadership Compass</p>
      <p class="front-author">Helena Marchbank</p>
      <p class="front-role">BUSINESS LEADERSHIP &amp; CHANGE EXPERT</p>
    </section>

  </div>
</div>
</body>
</html>
```